New florist business website design

Number 1 want is an easy to navigate & check out website
Needs to be beautiful and eye catching as well.
This is an online only business (no shop front)
Rustic and blush pinks, neutrals, woods, leaves
Customers need to be able to go onto my website, select something they want to buy but have the option to use a drop down box to change colours of the flowers, or add notes to make changes to the arrangement

Industry/Entity Type

Florist

Coding

Coded - Design and coding required

Number of Pages Required

5+ page

Colors
f9d9e8
fff2ec
fffefc

Requirements
Must have
• Drop down menu to take you to other pages for Arrangements, bouquets, everlasting arrangements, gifts, contact
Be able to purchase and “add to basket”
Checkout page
Nice to have
• Be able to add my own photos once I’ve taken new ones
Should not have
• Tacky images or clip art

```html
<!DOCTYPE html>
<html lang="en">
<head>
<meta charset="utf-8">
<title>Petal &amp; Fern — Florist</title>
<link rel="stylesheet" href="https://fonts.googleapis.com/css2?family=Josefin+Sans:wght@300;400;600&family=Cormorant+Garamond:wght@400;500&family=Great+Vibes&display=swap">
<style>
:root{
  --blush:#f9d9e8;
  --cream:#fff2ec;
  --paper:#fffefc;
  --peach:#fbe3cf;
  --pink:#ef5d97;
  --pink-soft:#f7c6d9;
  --ink:#1e1a1b;
  --muted:#5a4d50;
  --sky:#2aa8d8;
  --marigold:#f4a62a;
}
*{margin:0;padding:0;box-sizing:border-box}
html,body{width:1200px;height:4850px;overflow:hidden}
body{position:relative;background:var(--cream);font-family:'Cormorant Garamond',serif;color:var(--ink)}
.abs{position:absolute}
.sans{font-family:'Josefin Sans',sans-serif}
.photo{position:absolute;border-radius:10px}

/* header */
.site-header{position:absolute;left:0;top:0;width:1200px;height:150px;background:var(--blush)}
.brand{position:absolute;left:147px;top:50px;display:flex;align-items:center;gap:10px;font-family:'Josefin Sans',sans-serif;font-size:30px;font-weight:300;color:var(--ink)}
.brand-dot{width:14px;height:14px;border-radius:50%;background:var(--pink)}
.topbar{position:absolute;top:24px;left:505px;display:flex;align-items:center;gap:20px;font-family:'Josefin Sans',sans-serif;font-size:12px;color:var(--ink)}
.topbar .pinkicon{color:var(--pink)}
.social{display:flex;gap:8px}
.social span{width:20px;height:20px;border-radius:50%;background:var(--pink);display:block}
.search{position:absolute;left:358px;top:98px;width:273px;height:34px;background:var(--paper);border-radius:17px;font-family:'Josefin Sans',sans-serif;font-size:11px;color:#bbb;padding:11px 22px}
.search svg{position:absolute;right:14px;top:10px}
.nav{position:absolute;top:108px;font-family:'Josefin Sans',sans-serif;font-size:12px}

/* hero */
.hero{position:absolute;left:0;top:150px;width:1200px;height:585px;background:linear-gradient(90deg,var(--cream) 0%,var(--paper) 45%,var(--paper) 100%)}
.hero-kicker{position:absolute;left:145px;top:290px;font-size:22px;color:var(--pink)}
.hero-title{position:absolute;left:145px;top:325px;font-family:'Josefin Sans',sans-serif;font-weight:300;font-size:42px;line-height:56px}
.btn-ghost{position:absolute;background:var(--peach);border-radius:20px;font-family:'Josefin Sans',sans-serif;font-size:13px;display:flex;align-items:center;justify-content:center;color:var(--ink)}
.btn-pink{position:absolute;background:var(--pink);color:#fff;border-radius:22px;font-family:'Josefin Sans',sans-serif;display:flex;align-items:center;justify-content:center;text-transform:uppercase}

/* features */
.feature{position:absolute;top:830px;display:flex;gap:18px;align-items:center}
.feature h4{font-family:'Josefin Sans',sans-serif;font-weight:400;font-size:21px}
.feature p{font-size:14px;color:var(--pink)}

.section-title{position:absolute;left:0;width:1200px;text-align:center;font-family:'Josefin Sans',sans-serif;font-weight:300;letter-spacing:1px}

.card-name{position:absolute;width:286px;text-align:center;font-family:'Josefin Sans',sans-serif;font-size:17px;font-weight:300}
.card-price{position:absolute;width:286px;text-align:center;font-size:15px}

.promise{position:absolute;top:2380px;width:320px;text-align:center}
.promise h4{font-family:'Josefin Sans',sans-serif;font-weight:400;font-size:17px;margin-top:24px}
.promise p{font-size:14px;line-height:20px;margin-top:6px;color:var(--muted)}
.promise .tag{display:inline-block;margin-top:10px;background:var(--pink);color:#fff;font-family:'Josefin Sans',sans-serif;font-size:10px;padding:7px 16px 5px;border-radius:14px}

.sale-script{position:absolute;font-family:'Great Vibes',cursive;color:#fff;font-size:110px;line-height:1}

.why{position:absolute;left:145px;display:flex;gap:22px;width:380px}
.why h4{font-family:'Josefin Sans',sans-serif;font-weight:400;font-size:19px;color:var(--pink)}
.why p{font-size:14px;line-height:18px;margin-top:6px}
.why-icon{width:44px;height:44px;flex:none}
.why-sep{position:absolute;left:145px;width:350px;height:1px;background:var(--pink-soft)}

footer{position:absolute;left:0;top:4560px;width:1200px;height:272px;background:var(--cream)}
.fcol{position:absolute;top:78px;font-size:13px;line-height:26px}
.fcol h5{font-family:'Josefin Sans',sans-serif;font-weight:400;font-size:17px;margin-bottom:6px}
.finput{width:140px;height:22px;background:var(--paper);border-radius:11px;font-size:10px;color:#999;padding:4px 10px;margin-bottom:14px}
.copyright{position:absolute;left:0;top:4832px;width:1200px;height:18px;background:var(--ink);color:#ddd;font-size:9px;text-align:center;line-height:18px;font-family:'Josefin Sans',sans-serif}
</style>
</head>
<body>

<!-- header -->
<header class="site-header">
  <div class="brand"><span class="brand-dot"></span>Petal &amp; Fern</div>
  <div class="topbar">
    <span><span class="pinkicon">&#9742;</span> 555-0142-318</span>
    <span><span class="pinkicon">&#9993;</span> hello@petalandfern.com</span>
    <span class="social"><span></span><span></span><span></span></span>
    <span>My Account</span>
    <svg width="18" height="16" viewBox="0 0 18 16"><path d="M9 15 1.5 7.5A4 4 0 0 1 9 3a4 4 0 0 1 7.5 4.5Z" fill="#1e1a1b"/></svg>
    <svg width="18" height="18" viewBox="0 0 18 18" fill="none" stroke="#1e1a1b" stroke-width="1.6"><path d="M3 6h12l-1 10H4Z"/><path d="M6 6a3 3 0 0 1 6 0"/></svg>
  </div>
  <div class="search">Search
    <svg width="14" height="14" viewBox="0 0 14 14" fill="none" stroke="#ef5d97" stroke-width="1.6"><circle cx="6" cy="6" r="4.5"/><path d="M9.5 9.5 13 13"/></svg>
  </div>
  <span class="nav" style="left:674px">Home</span>
  <span class="nav" style="left:762px">Shop &#8964;</span>
  <span class="nav" style="left:848px">About</span>
  <span class="nav" style="left:937px">Blog</span>
  <span class="nav" style="left:1012px">Contact</span>
</header>

<!-- hero -->
<section class="hero">
  <div class="photo" role="img" aria-label="Close-up of pink roses and white lilies" style="left:500px;top:0;width:700px;height:560px;border-radius:0;background:radial-gradient(circle at 60% 40%,#fffafa 0%,#f6d5df 35%,#e87fa3 65%,#cfe3b0 100%)"></div>
  <svg class="abs" style="left:0;top:470px" width="1200" height="115" viewBox="0 0 1200 115" preserveAspectRatio="none">
    <path d="M0 60 C300 20 600 120 1200 40 L1200 115 L0 115Z" fill="#f5b6cf"/>
    <path d="M0 75 C320 35 640 130 1200 60 L1200 115 L0 115Z" fill="#fff2ec"/>
  </svg>
  <div class="abs" style="left:1005px;top:523px;display:flex;gap:6px">
    <span style="width:10px;height:10px;border-radius:50%;background:var(--pink)"></span>
    <span style="width:10px;height:10px;border-radius:50%;background:#fff"></span>
    <span style="width:10px;height:10px;border-radius:50%;background:#fff"></span>
  </div>
</section>
<div class="hero-kicker">Let's Fall in Love</div>
<h1 class="hero-title">Beauty Flowers that<br>Brings happiness</h1>
<div class="btn-ghost" style="left:145px;top:456px;width:140px;height:38px">SHOP NOW</div>

<!-- features -->
<div class="feature" style="left:145px">
  <svg width="60" height="52" viewBox="0 0 60 52" fill="none" stroke="#ef5d97" stroke-width="1.6"><rect x="2" y="2" width="56" height="36" rx="3"/><path d="M22 38v8h16v-8M16 48h28"/><rect x="14" y="12" width="22" height="12" rx="2"/></svg>
  <div><h4>Order Online</h4><p>Order bouquet via Online</p></div>
</div>
<div class="feature" style="left:458px">
  <svg width="66" height="48" viewBox="0 0 66 48" fill="none" stroke="#ef5d97" stroke-width="1.6"><rect x="2" y="6" width="38" height="28" rx="2"/><path d="M40 14h14l10 12v8H40"/><circle cx="14" cy="38" r="6"/><circle cx="52" cy="38" r="6"/></svg>
  <div><h4>Free Shipping</h4><p>For all orders from $100</p></div>
</div>
<div class="feature" style="left:791px">
  <svg width="56" height="52" viewBox="0 0 56 52" fill="none" stroke="#ef5d97" stroke-width="1.6"><circle cx="18" cy="16" r="10"/><circle cx="38" cy="22" r="10"/><path d="M18 26v24M38 32l-12 18"/></svg>
  <div><h4>More Freshness</h4><p>Bouquet are fresh &amp; blooms</p></div>
</div>

<!-- new arrivals -->
<section class="abs" style="left:0;top:960px;width:1200px;height:1230px;background:linear-gradient(180deg,var(--peach) 0%,#fde9df 70%,#fbe0e2 100%)"></section>
<div class="photo" role="img" aria-label="Sprig of white blossom with leaves" style="left:0;top:950px;width:180px;height:150px;border-radius:0;background:radial-gradient(ellipse at 40% 60%,#8aa76a 0%,rgba(138,167,106,0) 70%)"></div>
<div class="photo" role="img" aria-label="Sprig of white blossom with leaves" style="left:1020px;top:2070px;width:180px;height:170px;border-radius:0;background:radial-gradient(ellipse at 60% 50%,#a7c08a 0%,rgba(167,192,138,0) 70%)"></div>
<h2 class="section-title" style="top:1022px;font-size:34px">Our New Arrivals</h2>
<p class="section-title" style="top:1072px;font-family:'Cormorant Garamond',serif;font-size:15px;letter-spacing:0">A perfect blend of creativity, energy, communication, happiness and love. Let us arrange a smile for you.</p>

<div class="photo" role="img" aria-label="Bride holding a peach and white bridal bouquet" style="left:145px;top:1155px;width:286px;height:371px;background:linear-gradient(160deg,#eae4dc,#e6b7a4 55%,#9a8a78)"></div>
<div class="photo" role="img" aria-label="Round bouquet of pink roses" style="left:454px;top:1155px;width:286px;height:371px;background:radial-gradient(circle at 50% 40%,#f6b9c5,#e58da0 55%,#cdbab8)"></div>
<div class="photo" role="img" aria-label="Wicker basket of pink gerberas and roses" style="left:763px;top:1155px;width:286px;height:371px;background:linear-gradient(180deg,#f2f2f4 0%,#f4a5b8 55%,#c99a63 100%)"></div>
<div class="card-name" style="left:145px;top:1556px">Bridal Bouquet</div><div class="card-price" style="left:145px;top:1582px">$ 200.00</div>
<div class="card-name" style="left:454px;top:1556px">Personalized Bouquet</div><div class="card-price" style="left:454px;top:1582px">$ 300.00</div>
<div class="card-name" style="left:763px;top:1556px">Basket Bouquet</div><div class="card-price" style="left:763px;top:1582px">$ 300.00</div>

<div class="photo" role="img" aria-label="White orchid and blue hydrangea posy on wood" style="left:145px;top:1635px;width:286px;height:373px;background:linear-gradient(150deg,#8b5a3c,#f4f2f0 45%,#93a6d8 75%,#8b5a3c)"></div>
<div class="photo" role="img" aria-label="Flower girl with a red and pink bouquet in a garden" style="left:454px;top:1635px;width:286px;height:373px;background:linear-gradient(180deg,#3f6b3a,#6f9c57 45%,#d96b77 80%,#f2e4df)"></div>
<div class="photo" role="img" aria-label="Hand-tied bouquet of burgundy and white blooms" style="left:763px;top:1635px;width:286px;height:373px;background:linear-gradient(180deg,#eeeeee,#c98a8f 55%,#7b3a45 75%,#8aa38a)"></div>
<div class="card-name" style="left:145px;top:2036px">Tussy Mussy Bouquet</div><div class="card-price" style="left:145px;top:2062px">$ 200.00</div>
<div class="card-name" style="left:454px;top:2036px">Flower Girl Boutique</div><div class="card-price" style="left:454px;top:2062px">$ 300.00</div>
<div class="card-name" style="left:763px;top:2036px">Hand-Tied Bouquet</div><div class="card-price" style="left:763px;top:2062px">$ 300.00</div>
<div class="btn-pink" style="left:509px;top:2123px;width:181px;height:44px;font-size:15px">Shop More</div>

<svg class="abs" style="left:0;top:2140px" width="1200" height="90" viewBox="0 0 1200 90" preserveAspectRatio="none"><path d="M0 70 C300 20 700 20 1200 60 L1200 90 L0 90Z" fill="#fff2ec"/></svg>

<!-- promises -->
<h2 class="section-title" style="top:2275px;font-size:31px">Emotions dressed with lovely flowers</h2>
<div class="promise" style="left:100px">
  <svg width="56" height="52" viewBox="0 0 56 52" fill="none" stroke="#ef5d97" stroke-width="2"><path d="M4 6h8l6 28h26l6-20H15"/><circle cx="22" cy="44" r="4"/><circle cx="40" cy="44" r="4"/></svg>
  <h4>Delivering Your Emotions</h4><p>Send lovely flowers and gifts same<br>day to surprise your loved one</p><span class="tag">DELIVERY TERMS</span>
</div>
<div class="promise" style="left:440px">
  <svg width="56" height="56" viewBox="0 0 56 56" fill="none" stroke="#ef5d97" stroke-width="2"><circle cx="28" cy="28" r="25"/><circle cx="28" cy="28" r="18"/><path d="M19 28l6 6 12-12"/></svg>
  <h4>100% Fresh Flowers</h4><p>Fresh Flower Basket, Cut Flowers &amp;<br>more at lower price</p><span class="tag">RETURN POLICY</span>
</div>
<div class="promise" style="left:778px">
  <svg width="56" height="52" viewBox="0 0 56 52" fill="none" stroke="#ef5d97" stroke-width="2"><path d="M10 8c-4 4-4 12 6 24s20 16 24 12l3-4-8-6-4 3c-4-2-10-8-12-12l3-4-6-8Z"/><rect x="30" y="4" width="22" height="14" rx="3"/></svg>
  <h4>Online Flowers Delivery</h4><p>24/7 Flower &amp; Bouquet delivery<br>with hassle free support</p><span class="tag">SUPPORT TERMS</span>
</div>

<!-- spring sale -->
<div class="photo" role="img" aria-label="Orange poppies against a bright turquoise sky" style="left:0;top:2628px;width:1200px;height:499px;border-radius:0;background:linear-gradient(115deg,#1a9fd4 0%,#55c4e4 35%,#f5b73c 70%,#e8922a 100%)"></div>
<svg class="abs" style="left:0;top:2610px" width="1200" height="60" viewBox="0 0 1200 60" preserveAspectRatio="none"><path d="M0 0H1200V10C900 20 400 30 0 50Z" fill="#fff2ec"/></svg>
<svg class="abs" style="left:0;top:3070px" width="1200" height="60" viewBox="0 0 1200 60" preserveAspectRatio="none"><path d="M0 20C300 60 700 0 1200 30V60H0Z" fill="#fff2ec"/></svg>
<div class="abs sans" style="left:226px;top:2742px;color:#fff;font-size:28px;font-weight:300">Take Upto 50% Off</div>
<div class="sale-script" style="left:140px;top:2768px">Spring</div>
<div class="sale-script" style="left:240px;top:2860px">Sale</div>
<div class="btn-ghost" style="left:245px;top:2984px;width:117px;height:30px;background:var(--paper);font-size:11px">SHOP NOW</div>

<!-- sale products -->
<section class="abs" style="left:0;top:3130px;width:1200px;height:960px;background:linear-gradient(180deg,var(--cream),#fde3e6)"></section>
<div class="photo" role="img" aria-label="White daisy sprig" style="left:0;top:3220px;width:140px;height:130px;border-radius:0;background:radial-gradient(ellipse,#f8f4ef 0%,rgba(255,255,255,0) 70%)"></div>
<div class="photo" role="img" aria-label="Pink rose and gypsophila bouquet" style="left:145px;top:3152px;width:286px;height:320px;background:radial-gradient(circle at 50% 40%,#f7c3d0,#eef0ea 60%,#d9d9d9)"></div>
<div class="photo" role="img" aria-label="Woman holding yellow sunflowers" style="left:454px;top:3152px;width:286px;height:320px;background:linear-gradient(180deg,#6e7c5a,#c7a58e 40%,#f3d33a 75%,#efe8d6)"></div>
<div class="photo" role="img" aria-label="Dusky pink roses with greenery on wood" style="left:748px;top:3150px;width:330px;height:325px;border-radius:0;background:radial-gradient(circle,#e7b0b8,#8fa07a 60%,#b9bfc6)"></div>
<div class="card-name" style="left:145px;top:3506px">Tussy Mussy Bouquet</div><div class="card-price" style="left:145px;top:3536px">$ 200.00</div>
<div class="card-name" style="left:454px;top:3506px">Flower Girl Boutique</div><div class="card-price" style="left:454px;top:3536px">$ 300.00</div>
<div class="card-name" style="left:763px;top:3506px">Hand-Tied Bouquet</div><div class="card-price" style="left:763px;top:3536px">$ 300.00</div>

<div class="photo" role="img" aria-label="Pink peony and tulip posy" style="left:145px;top:3589px;width:286px;height:320px;background:radial-gradient(circle at 50% 45%,#f8d0da,#e07aa3 55%,#8aa37a)"></div>
<div class="photo" role="img" aria-label="Woman in red holding red roses" style="left:454px;top:3589px;width:286px;height:320px;background:radial-gradient(circle at 50% 60%,#e7343f,#b31c2a 55%,#3f5a2e)"></div>
<div class="photo" role="img" aria-label="Hand-tied bouquet of orange and pink flowers" style="left:763px;top:3589px;width:286px;height:320px;background:radial-gradient(circle at 50% 45%,#f08a6a,#d84a6e 45%,#46663c 75%,#5a4030)"></div>
<div class="card-name" style="left:145px;top:3941px">Tussy Mussy Bouquet</div><div class="card-price" style="left:145px;top:3971px">$ 200.00</div>
<div class="card-name" style="left:454px;top:3941px">Flower Girl Boutique</div><div class="card-price" style="left:454px;top:3971px">$ 300.00</div>
<div class="card-name" style="left:763px;top:3941px">Hand-Tied Bouquet</div><div class="card-price" style="left:763px;top:3971px">$ 300.00</div>

<!-- florist -->
<section class="abs" style="left:0;top:4050px;width:1200px;height:510px;background:linear-gradient(90deg,var(--paper) 0%,var(--paper) 45%,var(--blush) 100%)"></section>
<div class="photo" role="img" aria-label="Cluster of pink roses" style="left:527px;top:4040px;width:673px;height:520px;border-radius:0;background:radial-gradient(circle at 65% 50%,#f27ea3,#f6b3c8 50%,rgba(255,242,236,0) 80%)"></div>
<h2 class="abs sans" style="left:145px;top:4118px;font-size:29px;font-weight:300">The Florist - to fulfill your bouquet needs</h2>
<div class="why" style="top:4202px">
  <svg class="why-icon" viewBox="0 0 44 44" fill="none" stroke="#ef5d97" stroke-width="1.8"><path d="M38 22a16 16 0 1 1-5-11.6"/><path d="M34 4v7h-7"/><text x="11" y="27" font-size="11" fill="#ef5d97" stroke="none" font-family="Josefin Sans">24h</text></svg>
  <div><h4>Adorning Life Moments</h4><p>Vitae et leo duis ut diam quam. Aliquam vestibulum morbi blandit.</p></div>
</div>
<div class="why-sep" style="top:4290px"></div>
<div class="why" style="top:4315px">
  <svg class="why-icon" viewBox="0 0 44 44" fill="none" stroke="#ef5d97" stroke-width="1.8"><path d="M22 3l5 5h7v7l5 5-5 5v7h-7l-5 5-5-5h-7v-7l-5-5 5-5V8h7Z"/></svg>
  <div><h4>100% Freshness Guaranteed</h4><p>Turpis egestas pretium aenean pharetra magna ac placerat.</p></div>
</div>
<div class="why-sep" style="top:4403px"></div>
<div class="why" style="top:4428px">
  <svg class="why-icon" viewBox="0 0 44 44" fill="none" stroke="#ef5d97" stroke-width="1.8"><path d="M3 8h6l5 20h20l5-14H11"/><circle cx="17" cy="36" r="3"/><circle cx="31" cy="36" r="3"/></svg>
  <div><h4>Delivering Smiles Daily!</h4><p>Aliquam id diam maecenas ultricies mi eget mauris pharetra et.</p></div>
</div>

<!-- footer -->
<footer>
  <div class="brand" style="left:150px;top:110px;font-size:32px"><span class="brand-dot"></span>Petal &amp; Fern</div>
  <div class="fcol" style="left:384px"><h5>Navigation</h5>Home<br>Shop<br>About<br>Blog<br>Contact</div>
  <div class="fcol" style="left:527px"><h5>Help</h5>Search<br>Help<br>Information<br>Privacy Policy<br>Shipping Details</div>
  <div class="fcol" style="left:697px"><h5>Contact Us</h5>Phone: 555-0142-318<br>Fax: 555-0142-318<br>hello@petalandfern.com
    <div style="display:flex;gap:8px;margin-top:12px">
      <span style="width:28px;height:28px;border:1px solid var(--ink);border-radius:50%"></span>
      <span style="width:28px;height:28px;border:1px solid var(--ink);border-radius:50%"></span>
      <span style="width:28px;height:28px;border:1px solid var(--ink);border-radius:50%"></span>
    </div>
  </div>
  <div class="fcol" style="left:910px"><h5>Subscribe</h5>
    <div class="finput">Name</div>
    <div class="finput">Email</div>
    <div style="width:82px;height:20px;background:var(--pink);color:#fff;border-radius:10px;font-size:10px;text-align:center;line-height:20px">Subscribe</div>
  </div>
</footer>
<div class="copyright">Copyright © Petal &amp; Fern 2021. All rights reserved</div>

</body>
</html>
```